Global (re)insurance broker needs a business card design

We need a classic business card for our company that is headquartered in SG, with offices in Malaysia and Dubai. We specialise in insurance and reinsurance broking and consultancy for our global clients.

```html
<!DOCTYPE html>
<html lang="en">
<head>
<meta charset="utf-8">
<title>Korvell Business Card</title>
<link href="https://fonts.googleapis.com/css2?family=Montserrat:wght@300;400;700&family=Open+Sans:wght@400&display=swap" rel="stylesheet">
<style>
  :root {
    --stage: #2b2b2e;
    --card: #161616;
    --brand-blue: #2a4c9f;
    --brand-mint: #c4dfb9;
    --ink-light: #f2f2f2;
  }
  * { box-sizing: border-box; margin: 0; padding: 0; }
  html, body {
    width: 1200px; height: 947px; overflow: hidden;
    background: var(--stage);
  }
  .stage {
    width: 1200px; height: 947px;
    display: flex; align-items: center; justify-content: center; gap: 44px;
  }
  .card {
    position: relative;
    width: 540px; height: 310px;
    background: var(--card);
    border: 3px solid var(--brand-blue);
    border-radius: 24px;
    overflow: hidden;
    box-shadow: 0 18px 40px rgba(0,0,0,.45);
  }
  .card--front {
    display: flex; align-items: center; justify-content: center;
  }
  .brand-name {
    font-family: "Montserrat", sans-serif;
    font-weight: 700;
    font-size: 92px;
    letter-spacing: 2px;
    color: var(--brand-mint);
  }
  .card--back .identity {
    position: absolute; top: 92px; left: 48px;
    display: flex; align-items: center;
  }
  .person { text-align: right; padding-right: 22px; }
  .person-name {
    font-family: "Montserrat", sans-serif; font-weight: 700;
    font-size: 30px; color: var(--brand-blue); line-height: 1.1;
  }
  .person-title {
    font-family: "Montserrat", sans-serif; font-weight: 300;
    font-size: 19px; color: var(--ink-light); margin-top: 4px;
  }
  .divider {
    width: 2px; height: 82px; background: var(--brand-blue);
  }
  .contact-list {
    list-style: none; padding-left: 20px;
    font-family: "Open Sans", sans-serif; font-size: 15px;
    color: var(--ink-light);
  }
  .contact-list li {
    display: flex; align-items: center; gap: 9px; line-height: 24px;
  }
  .contact-list svg { width: 13px; height: 13px; fill: var(--brand-blue); flex: none; }
  .address-band {
    position: absolute; left: 0; right: 0; bottom: 26px; height: 36px;
    background: var(--brand-blue);
    display: flex; align-items: center; justify-content: center;
    font-family: "Open Sans", sans-serif; font-size: 15px;
    color: var(--ink-light); letter-spacing: .2px;
  }
</style>
</head>
<body>
<main class="stage">
  <section class="card card--front" aria-label="Card front">
    <span class="brand-name">KORVELL</span>
  </section>

  <section class="card card--back" aria-label="Card back">
    <div class="identity">
      <div class="person">
        <p class="person-name">Mira Lowe</p>
        <p class="person-title">Chief Operating Officer</p>
      </div>
      <div class="divider"></div>
      <ul class="contact-list">
        <li>
          <svg viewBox="0 0 16 16" aria-hidden="true"><path d="M3.6 1.2l2.4 2.4-1.4 2c.9 1.9 2.5 3.5 4.4 4.4l2-1.4 2.4 2.4-1.6 2.2C6.6 13 3 9.4 1.4 2.8z"/></svg>
          +65 9000 4321
        </li>
        <li>
          <svg viewBox="0 0 16 16" aria-hidden="true"><path d="M1 3h14v10H1z M1 3l7 5 7-5" stroke="#161616" stroke-width="1.2"/></svg>
          mira@korvell.com
        </li>
        <li>
          <svg viewBox="0 0 16 16" aria-hidden="true"><circle cx="8" cy="8" r="7"/></svg>
          www.korvell.com
        </li>
      </ul>
    </div>
    <div class="address-band">22 Harbour Lane, Meridian Tower #08-04, Singapore 048620</div>
  </section>
</main>
</body>
</html>
```